Word Template Designs for Offensive Security Professional Services Report

We need a Microsoft Word Template designed for our Offensive Security professional services reports which includes the following services:

RedTeaming
Network Penetration Testing
Web Application Penetration Testing
Wireless Penetration Testing
Social Engineering

The templates should include the following:
Cover Page design with our Logo included
Executive Summary Page design
Detailed Findings Page design
Design for Last Page

Lastly, I would also like a template I can use for all of my Statements of Work

Requirements
Must have
• Beautiful Eye Catching HD pictures that represent my Offensive Security projects
The design should flow well with our logo

```html
<!DOCTYPE html>
<html lang="en">
<head>
<meta charset="utf-8">
<title>Scope of Work Template Pages</title>
<link rel="stylesheet" href="https://fonts.googleapis.com/css2?family=Roboto:wght@400;500;700&family=Lato:wght@400;700&display=swap">
<style>
:root{
  --stage:#767676;
  --paper:#ffffff;
  --green:#5b8c3a;
  --green-dark:#2f4a1f;
  --ink:#222222;
  --black:#0b0b0b;
  --row-grey:#e4e4e4;
  --photo-dark:#06090d;
  --photo-blue:#0e3d60;
}
*{margin:0;padding:0;box-sizing:border-box}
html,body{width:676px;height:1200px;overflow:hidden;background:var(--stage)}
body{position:relative;font-family:"Lato",Arial,sans-serif;color:var(--ink)}
.page{position:absolute;width:236px;height:333px;background:var(--paper);overflow:hidden;box-shadow:0 2px 6px rgba(0,0,0,.35)}
.cover{left:221px;top:59px}
.revision{left:103px;top:417px}
.contents{left:378px;top:417px}
.phases{left:103px;top:770px}
.summary{left:378px;top:770px}
.abs{position:absolute}
.brand{position:absolute;text-align:center;width:100%}
.brand-mark{width:26px;height:26px;border-radius:50%;background:var(--green-dark);margin:0 auto;border:1.5px solid #9a9a9a}
.brand-name{font-family:"Roboto",Arial,sans-serif;font-weight:700;font-size:8.4px;color:var(--green-dark);margin-top:2px}
.cover-kicker{left:20px;top:64px;font-family:"Roboto",Arial,sans-serif;font-weight:500;font-size:8px;color:var(--green)}
.cover-title{left:20px;top:75px;font-family:"Roboto",Arial,sans-serif;font-weight:500;font-size:9.8px;line-height:12px;color:var(--green-dark)}
.cover-for{left:20px;top:119px;font-family:"Roboto",Arial,sans-serif;font-weight:500;font-size:7px;line-height:9px;color:var(--ink)}
.cover-art{left:0;top:0;width:236px;height:333px}
.cover-by{left:20px;top:220px;font-family:"Roboto",Arial,sans-serif;color:#fff;font-size:4.6px;line-height:5.7px}
.cover-by h3{font-size:7px;font-weight:500;line-height:8px}
.cover-by .gap{height:5px}
.cover-foot{left:0;top:306px;width:236px;height:27px;background:var(--green);display:flex;justify-content:space-around;align-items:center;font-family:"Roboto",Arial,sans-serif;font-size:4.2px;color:#fff}
.cover-foot span{display:flex;align-items:center;gap:2px}
.page-tag{position:absolute;left:0;width:24px;height:11px;background:var(--black);color:#fff;font-size:3.8px;line-height:11px;text-align:center}
.rev-title{left:0;top:14px;width:236px;text-align:center;font-family:"Roboto",Arial,sans-serif;font-weight:700;font-size:9.5px;color:var(--green)}
.rev-head{left:0;top:32px;width:236px;height:13px;background:var(--black);color:#fff;font-family:"Roboto",Arial,sans-serif;font-size:6.6px;line-height:13px}
.rev-row{left:0;top:48px;width:236px;font-size:3.8px}
.col1{position:absolute;left:15px}.col2{position:absolute;left:83px}.col3{position:absolute;left:165px}
.rev-row .col2{left:86px}.rev-row .col3{left:170px}
.toc-band{left:0;top:64px;width:236px;height:18px;background:var(--green);color:#fff;text-align:center;font-family:"Roboto",Arial,sans-serif;font-weight:700;font-size:11.5px;line-height:18px}
.toc-list{left:0;top:98px;width:236px;list-style:none}
.toc-list li{height:11.85px;line-height:11.85px;font-family:"Roboto",Arial,sans-serif;font-size:4.2px;padding:0 9px;display:flex;justify-content:space-between}
.toc-list li.major{background:var(--row-grey);font-weight:700}
.band{position:absolute;left:0;background:var(--green);color:#fff;font-family:"Roboto",Arial,sans-serif;font-weight:700;font-size:6px;padding-left:9px;display:flex;align-items:center}
.band.wide{width:236px;justify-content:center;font-size:10px;padding:0}
.copy{position:absolute;font-size:4px;line-height:5.2px;color:var(--ink)}
.summary .copy{left:7.5px;width:221px}
.phases .copy{left:9px;width:219px}
.lead{color:var(--green)}
.copy.note{font-size:3.6px;line-height:4.6px}
.checks{position:absolute;left:11px;width:210px;display:grid;grid-template-columns:1fr 1fr;row-gap:3.3px;font-size:4px}
.checks li{list-style:none}
.checks li::before{content:"\2713";color:var(--green);margin-right:3px}
.tests{position:absolute;left:26px;top:164px;width:200px;display:grid;grid-template-columns:99px 1fr;grid-auto-flow:column;grid-template-rows:repeat(7,9.5px);font-size:4px;list-style:none}
.tests li{position:relative;padding-left:6px;line-height:4.6px}
.tests li::before{content:"";position:absolute;left:0;top:0.8px;width:3.4px;height:3.4px;border-radius:50%;background:var(--green)}
.deliver{position:absolute;left:11px;width:215px;list-style:none;font-size:4px;line-height:5px}
.deliver li{position:relative;padding-left:5px;margin-bottom:3.5px}
.deliver li::before{content:"";position:absolute;left:0;top:1.6px;width:1.8px;height:1.8px;border-radius:50%;background:var(--green)}
.site{position:absolute;right:9px;font-size:4px;color:var(--green)}
.texture{position:absolute;left:0;top:250px;width:236px;height:83px;background:linear-gradient(180deg,rgba(255,255,255,0),rgba(220,228,236,.35))}
</style>
</head>
<body>

<section class="page cover">
  <svg class="abs cover-art" viewBox="0 0 236 333" aria-hidden="false">
    <defs>
      <linearGradient id="circuitTone" x1="0" y1="1" x2="1" y2="0">
        <stop offset="0" stop-color="#06090d"/>
        <stop offset="0.45" stop-color="#0a1a28"/>
        <stop offset="1" stop-color="#145277"/>
      </linearGradient>
    </defs>
    <g role="img" aria-label="Photo of a glowing blue circuit board with a padlock shield icon">
      <polygon points="0,202 236,113 236,303 0,303" fill="url(#circuitTone)"/>
    </g>
    <polygon points="0,190 236,107 236,113 0,202" fill="#5b8c3a"/>
    <polygon points="0,303 236,303 236,306 0,306" fill="#ffffff"/>
  </svg>

  <div class="brand" style="top:14px">
    <div class="brand-mark"></div>
    <div class="brand-name">Vantage Breach</div>
  </div>

  <p class="abs cover-kicker">SCOPE OF WORK :</p>
  <h1 class="abs cover-title">External, Internal Network,<br>Wireless and Web Application Penetration<br>Testing Engagement</h1>
  <p class="abs cover-for">PREPARED FOR :<br>[Client Name]</p>

  <div class="abs cover-by">
    <h3>PREPARED BY :</h3>
    <p>Daniel Harrow, CISSP, OSCE, OSCP</p>
    <p>[Company Name], LLC</p>
    <div class="gap"></div>
    <p>4120 Ridgeway Blvd Suite 210</p>
    <p>Austin Texas 78701</p>
    <p>www.vantage-breach.com</p>
    <div class="gap"></div>
    <p>Daniel.Harrow@Vantage-Breach.com</p>
    <p>Office 1800.555.0142</p>
    <p>Mobile: 512.555.0187</p>
    <p>August 2, 2018</p>
  </div>

  <footer class="abs cover-foot">
    <span><svg width="5" height="5" viewBox="0 0 10 10"><circle cx="5" cy="5" r="4.3" fill="none" stroke="#fff" stroke-width="0.9"/><path d="M3.4 2.8l1 1-.6.7c.4.8 1 1.4 1.8 1.8l.7-.6 1 1-.7.9C4.9 7.4 2.8 5.3 2.5 3.5z" fill="#fff"/></svg>1-800-555-0142</span>
    <span><svg width="5" height="4" viewBox="0 0 10 8"><rect x="0.5" y="0.5" width="9" height="7" fill="none" stroke="#fff"/><path d="M0.5 0.5L5 4.5 9.5 0.5" fill="none" stroke="#fff"/></svg>info@example.com</span>
    <span><svg width="5" height="5" viewBox="0 0 10 10"><circle cx="5" cy="5" r="4.3" fill="none" stroke="#fff" stroke-width="0.9"/><path d="M0.7 5h8.6M5 0.7c-2.4 2.6-2.4 6 0 8.6M5 0.7c2.4 2.6 2.4 6 0 8.6" fill="none" stroke="#fff" stroke-width="0.7"/></svg>www.vantage-breach.com</span>
  </footer>
</section>

<section class="page revision">
  <h2 class="abs rev-title">DOCUMENT REVISION CONTROL</h2>
  <div class="abs rev-head"><span class="col1">Revision Number</span><span class="col2">Revision</span><span class="col3">Revision Date</span></div>
  <div class="abs rev-row"><span class="col1">1.0</span><span class="col2">Initial</span><span class="col3">8/2/18</span></div>
  <div class="page-tag" style="top:319px">Page 2</div>
</section>

<section class="page contents">
  <div class="brand" style="top:10px">
    <div class="brand-mark"></div>
    <div class="brand-name">Vantage Breach</div>
  </div>
  <h2 class="abs toc-band">TABLE OF CONTENTS</h2>
  <ul class="abs toc-list">
    <li><span>TABLE OF CONTENTS</span><span>3</span></li>
    <li class="major"><span>PROPOSAL SUMMARY</span><span>4</span></li>
    <li><span>ENGAGEMENT OVERVIEW</span><span>4</span></li>
    <li><span>Phase One: External Network Penetration Testing</span><span>4</span></li>
    <li><span>Phase Two: Internal Network Penetration Testing</span><span>4</span></li>
    <li><span>Phase Three: Wireless Penetration Testing</span><span>5</span></li>
    <li><span>Phase Four: Targeted Web Application Penetration Testing</span><span>5</span></li>
    <li><span>ENGAGEMENT DELIVERABLES</span><span>6</span></li>
    <li><span>PHASE SPECIFIC TASKS</span><span>7</span></li>
    <li><span>Phase One: External Network Penetration Testing</span><span>7</span></li>
    <li><span>Phase Two: Internal Network Penetration Testing</span><span>9</span></li>
    <li><span>Phase Three: Wireless Penetration Testing</span><span>11</span></li>
    <li><span>Phase Four: Targeted Web Application Penetration Testing</span><span>12</span></li>
    <li class="major"><span>ABOUT [COMPANY NAME]</span><span>15</span></li>
    <li><span>CONSULTANT PROFILE</span><span>15</span></li>
    <li class="major"><span>SCOPE APPROVAL</span><span>16</span></li>
    <li><span>CLIENT ACTIVITY CHECKLIST</span><span>16</span></li>
    <li><span>ACKNOWLEDGEMENTS</span><span>16</span></li>
  </ul>
  <div class="page-tag" style="top:316px">Page 3</div>
</section>

<section class="page phases">
  <div class="texture" role="img" aria-label="Faint network line pattern"></div>
  <h2 class="band" style="top:10.7px;height:10.7px;width:162px">PHASE THREE:WIRELESS PENETRATION TESTING</h2>
  <p class="copy" style="top:24px">[Company Name] will assess[Client Name] guest and production wireless networks. During testing, [Company Name] will attempt to gain access to hosts belonging to [Client Name]' internal network presence and wireless controllers. [Company Name] will exploit vulnerabilities identified during the vulnerability identification process. After a system or information is compromised, [Company Name]will gather appropriate evidence for proof of information or system compromise.</p>
  <p class="copy" style="top:54px">[Company Name] will conduct this work on-site while performing the assessment in collaboration with [Client Name]. After the assessment is complete, [Company Name] will develop a formal report that will include the items described in the Final Report Summary.</p>

  <h2 class="band" style="top:75.5px;height:10.5px;width:218px">PHASE FOUR: TARGETED WEB APPLICATION PENETRATION TESTING</h2>
  <p class="copy" style="top:87.6px">[Company Name] will conduct a Targeted Web Application Penetration Testing assessment of the target web application and supporting services as anunauthorized/unauthenticated and authorized/authenticated users'perspective to determine the exposed vulnerabilities that are accessible to an attacker.</p>
  <p class="copy" style="top:107px"><span class="lead">Unauthorized/Unauthenticated</span> – An Unauthenticated Assessment of your web application gives a realistic view of what an attacker with a simple Internet connection and no privileges would be able to access, find, and possibly exploit. This type of assessment tests the strengths of your application's authentication mechanism(s) and any other vulnerability associated with the application.</p>
  <p class="copy" style="top:131px"><span class="lead">Authorized/Authenticated</span> – Anauthenticated Assessment of your web application gives a realistic view of what an attacker with basic and administrative privileges would be able to access, find, and possibly exploit. This type of assessment tests the strengths of your applications to withstand attacks by authorized users who have valid credentials to authenticate to the application.</p>
  <p class="copy" style="top:156px">Additional testing may include the following :</p>
  <ul class="tests">
    <li>Information Leakage</li>
    <li>Session Management</li>
    <li>Default Configurations</li>
    <li>Authentication abuse</li>
    <li>Client-Side Cache</li>
    <li>Authorization exploitation</li>
    <li>SQL Injection, (backend database enumeration and manipulation)</li>
    <li>OS Command Injection</li>
    <li>Local and Remote File Inclusion</li>
    <li>Cross Site Request Forgery</li>
    <li>Application and Business Logic Flaws</li>
    <li>Proper Input Validation</li>
    <li>Privilege Escalation Opportunities</li>
    <li>Client-Side Code</li>
    <li>Server-Side Input Validation</li>
  </ul>
  <p class="copy" style="top:234px">[Company Name] follows a well-developed and proven methodology to assess the security of web-based applications as defined in the specific tasks in the next section. After the assessment is complete, [Company Name] will develop a formal report that will include the items described in the Final Report Summary.</p>

  <h2 class="band" style="top:257px;height:10.5px;width:102px">ENGAGEMENT DELIVERABLES</h2>
  <p class="copy" style="top:270.5px">[Company Name] will provide the following Deliverables to [Client Name]:</p>
  <ul class="deliver" style="top:279px">
    <li>Weekly Status Updates if applicable</li>
    <li>Final Report and Presentation delivered at the end of the engagement</li>
    <li>Onsite Q&amp;A session with our consultants to discuss the process, findings, and recommendations, and answer questions related to the engagement.</li>
  </ul>
  <div class="page-tag" style="top:319px">Page 5</div>
  <span class="site" style="top:322px">www.vantage-breach.com</span>
</section>

<section class="page summary">
  <div class="texture" role="img" aria-label="Faint network line pattern"></div>
  <h2 class="band wide" style="top:13.5px;height:15.5px">PROPOSAL SUMMARY</h2>
  <p class="copy" style="top:35px">[Company Name] is proud to present this multi-phase Scope of Work to [Client Name]to meet theirPenetration TestingRequirements.[Company Name] LLC's security consultants have expert knowledge in Network Security and Web Applications, Security Controls, process and procedures, best practices, vulnerabilities and countermeasures. Our security consultantswill perform the penetration testing presented in this Scope of Work.</p>

  <h2 class="band" style="top:68px;height:11px;width:88px">ENGAGEMENT OVERVIEW</h2>
  <p class="copy" style="top:83px">Based on the information provided, [Company Name] understands that [Client Name]objectives are to have [Company Name] LLC provide penetration testing, ethical hacking and risk management services to [Client Name]to help ensure that the systems are working in a safe secure manner in every respect and by ensuring the proper preservation of all data's Confidentiality, Integrity, and Availability (CIA).</p>
  <p class="copy" style="top:106px">From [Company Name]'s understanding, [Client Name]has requested that the penetration testing be performed from a grey box perspective to determine the exposed vulnerabilities of the networks, applications and wireless implementations.</p>
  <p class="copy lead" style="top:128px">In response to these requirements, [Company Name] will perform the following services :</p>
  <ul class="checks" style="top:136px">
    <li>External Network Penetration Testing</li>
    <li>Internal Network Penetration Testing</li>
    <li>Wireless Network Penetration Testing</li>
    <li>Targeted Web Application Penetration Testing</li>
  </ul>

  <h2 class="band" style="top:155px;height:11px;width:190px">PHASE ONE: EXTERNAL NETWORK PENETRATION TESTING</h2>
  <p class="copy" style="top:171px">[Company Name] will conducta Network Penetration Testingassessment of the external network, aka the Internet presence to help identify existing vulnerabilities and their associated risks. [Company Name] will discover and identify hosts belonging to [Client Name] external network, identify vulnerabilities and exploit vulnerabilities identified during the ethical hacking process. After a system is compromised, the vulnerabilities and any applicable exploits will be documented in a detailed, repeatable process.</p>
  <p class="copy" style="top:201px">[Company Name] will conduct this work remotely while performing the Network Penetration Testing assessment in collaboration with [Client Name] personnel.After the assessment is complete, [Company Name] will develop a formal report that will include the items described in the Final Report Summary.</p>

  <h2 class="band" style="top:224px;height:11px;width:190px">PHASE TWO: INTERNAL NETWORK PENETRATION TESTING</h2>
  <p class="copy" style="top:240px">[Company Name] will conduct a penetration test of the [Client Name] internal network, aka their private LAN. [Company Name] will exploit vulnerabilities identified during the vulnerability identification process. After a system is compromised, the vulnerabilities and any applicable exploits will be documented in a detailed, repeatable process.</p>
  <p class="copy" style="top:260px">[Company Name] will conduct this work onsite initially and remotely after deploying [Company Name]'s internal network attack server. The Network Penetration Testing will be conducted in collaboration with [Client Name] personnel.After the assessment is complete, [Company Name] will develop a formal report that will include the items described in the Final Report Summary.</p>
  <p class="copy note" style="top:288px"><b>Note :</b> The attack server's purpose is to facilitate internal network penetration testing efforts from a remote offsite location. This will help emulate an attacker who has gained access to the internal network and is outside of the organization. No Denial of Service or testing outside of the internal network penetration testing efforts will be conducted via the attack server.</p>
  <div class="page-tag" style="top:316px">Page 4</div>
  <span class="site" style="top:319px">www.vantage-breach.com</span>
</section>

</body>
</html>
```